Card design for orthopaedic surgeons working as The Brightwater Joint Centre

Business cards, letterhead

Colors

Designer to choose colors to be used in the design.

Requirements
Must have
• Late addition.
• Cards letterhead must have logos of
• Crestmoor Lindell College of Surgeons
• Varenwood Bone Health Association
Nice to have
• Back of card to have space for appointment time to be added by hand and some blank space for writing incidental other notes.

```html
<!DOCTYPE html>
<html lang="en">
<head>
<meta charset="utf-8">
<title>The Brightwater Joint Centre – Business Card</title>
<link rel="stylesheet" href="https://fonts.googleapis.com/css2?family=Lato:wght@400;700&family=Roboto:wght@700&display=swap">
<style>
  :root {
    --backdrop: #1f1f1f;
    --card-white: #ffffff;
    --brand-blue: #33b0fb;
    --accent-blue: #2aa3ec;
    --ink: #1c1c1c;
    --on-blue: #ffffff;
  }
  * { margin: 0; padding: 0; box-sizing: border-box; }
  html, body {
    width: 1200px; height: 900px; overflow: hidden;
    background: var(--backdrop);
  }
  .canvas { position: relative; width: 1200px; height: 900px; }

  .card { position: absolute; top: 200px; width: 310px; height: 502px; }
  .card--front {
    left: 253px; background: var(--card-white);
    border-radius: 62px 0 62px 0;
  }
  .card--back {
    left: 627px; background: var(--brand-blue);
    border-radius: 0 62px 0 62px;
  }

  .brand-name {
    font-family: "Lato", sans-serif; font-weight: 400;
    white-space: nowrap;
  }
  .card--front .brand-name {
    position: absolute; top: 152px; left: 0; width: 100%;
    text-align: center; font-size: 17px; color: var(--accent-blue);
  }
  .card--back .brand-name {
    position: absolute; left: 50%; top: 50%;
    transform: translate(-50%, -50%) rotate(-90deg);
    font-size: 21px; color: var(--on-blue); letter-spacing: 0.2px;
  }

  .contact { position: absolute; left: 33px; top: 328px; font-family: "Lato", sans-serif; color: var(--ink); }
  .contact__name {
    font-family: "Roboto", Arial, sans-serif; font-weight: 700;
    font-size: 18px; color: var(--accent-blue); line-height: 20px;
  }
  .contact__role { font-size: 14px; line-height: 17px; margin-bottom: 6px; }
  .contact__line { display: flex; align-items: center; gap: 4px; font-size: 14px; line-height: 19px; }
  .contact__line svg { width: 13px; height: 13px; flex: none; }
  .contact__address { margin-top: 6px; font-size: 14px; line-height: 18px; }
</style>
</head>
<body>
<main class="canvas">
  <section class="card card--front" aria-label="Card front">
    <p class="brand-name">The Brightwater Joint Centre</p>

    <div class="contact">
      <p class="contact__name">MARCUS ELLERY</p>
      <p class="contact__role">Managing Director</p>
      <p class="contact__line">
        <svg viewBox="0 0 14 14" aria-hidden="true"><path fill="#2aa3ec" d="M1 5c0-2 3-3 6-3s6 1 6 3v1h-3V5H4v1H1zM3 7h8l1.5 5h-11z"/><circle cx="7" cy="9.5" r="1.4" fill="#fff"/></svg>
        044-555 018 274
      </p>
      <p class="contact__line">
        <svg viewBox="0 0 14 14" aria-hidden="true"><rect x="1" y="3" width="12" height="8" fill="#2aa3ec"/><path d="M1 3l6 5 6-5" fill="none" stroke="#fff" stroke-width="1"/></svg>
        info@brightwatermail.com
      </p>
      <p class="contact__line">
        <svg viewBox="0 0 14 14" aria-hidden="true"><circle cx="7" cy="7" r="6" fill="#2aa3ec"/><path d="M4 4c2 1 2 3 1 4s1 3 2 3M9 3c-1 2 1 3 3 3" fill="none" stroke="#fff" stroke-width="1"/></svg>
        www.brightwaterjoint.com
      </p>
      <p class="contact__address">421, Address line here<br>Country Name, 45452</p>
    </div>
  </section>

  <section class="card card--back" aria-label="Card back">
    <p class="brand-name">The Brightwater Joint Centre</p>
  </section>
</main>
</body>
</html>
```